Business Card for Coastal Tundrabridge Advisory

We need a business card for Coastal Tundrabridge Advisory. The company website address is provided below. The company logo is attached. We provide specialized permafrost services to the mining, transportation, and oil & gas industries. The card should be prepared for:
Matthias Korhonen, PhD.
Coastal Tundrabridge Advisory
PO Box 418259
Quillwater, Alaska 99642
Direct: +1-907-555-0143
Email: mkorhonen@tundrabridgeadvisory.example
Website: www.coastaltundrabridgeadvisory.example

```html
<!DOCTYPE html>
<html lang="en">
<head>
<meta charset="utf-8">
<title>Coastal Tundrabridge Advisory – Business Card</title>
<link rel="stylesheet" href="https://fonts.googleapis.com/css2?family=Roboto:wght@300;400;700&display=swap">
<style>
  :root {
    --backdrop: #232323;
    --card: #111723;
    --ink: #ffffff;
    --ink-soft: #d9dde6;
    --emboss: #22346e;
  }
  * { margin: 0; padding: 0; box-sizing: border-box; }
  html, body { width: 1200px; height: 711px; overflow: hidden; }
  body {
    background: var(--backdrop);
    font-family: "Roboto", Arial, sans-serif;
    color: var(--ink);
    position: relative;
  }
  .card {
    position: absolute;
    top: 201px;
    width: 540px;
    height: 309px;
    background: var(--card);
    border-radius: 18px;
    overflow: hidden;
  }
  .card--back { left: 45px; }
  .card--front { left: 615px; }

  /* Back */
  .back-wordmark {
    position: absolute;
    left: 0; right: 0; top: 92px;
    text-align: center;
    font-weight: 700;
    font-size: 30px;
    line-height: 1.15;
    letter-spacing: 1px;
    color: var(--emboss);
    text-transform: uppercase;
  }
  .services {
    position: absolute;
    left: 0; right: 0; bottom: 26px;
    text-align: center;
  }
  .services__title {
    font-weight: 700;
    font-size: 10.5px;
    letter-spacing: .3px;
    margin-bottom: 4px;
  }
  .services__text {
    font-size: 10px;
    color: var(--ink-soft);
  }

  /* Front */
  .name-block {
    position: absolute;
    left: 0; top: 30px;
    padding-left: 30px;
    border-left: 12px solid var(--ink);
  }
  .name {
    font-size: 23px;
    line-height: 1.1;
  }
  .name__first { font-weight: 700; }
  .name__last { font-weight: 300; }
  .credential {
    font-size: 15px;
    font-weight: 400;
    line-height: 1.2;
  }
  .front-wordmark {
    position: absolute;
    right: 26px; top: 30px;
    text-align: right;
    font-weight: 700;
    font-size: 16px;
    line-height: 1.15;
    letter-spacing: .8px;
    text-transform: uppercase;
    color: var(--ink);
  }
  .address {
    position: absolute;
    left: 42px; bottom: 26px;
    font-size: 11.5px;
    line-height: 1.45;
    font-weight: 400;
  }
  .contacts {
    position: absolute;
    right: 24px; bottom: 26px;
    list-style: none;
    font-size: 11px;
    line-height: 1.6;
    text-align: right;
  }
  .contacts li {
    display: flex;
    justify-content: flex-end;
    align-items: center;
    gap: 6px;
  }
  .contacts svg { width: 11px; height: 11px; fill: var(--ink); flex: none; }
</style>
</head>
<body>

<section class="card card--back" aria-label="Card back">
  <div class="back-wordmark">Coastal Tundrabridge<br>Advisory</div>
  <div class="services">
    <p class="services__title">OUR SERVICES</p>
    <p class="services__text">We provide specialized permafrost services to the mining, transportation, and oil &amp; gas industries</p>
  </div>
</section>

<section class="card card--front" aria-label="Card front">
  <div class="name-block">
    <p class="name"><span class="name__first">Matthias</span> <span class="name__last">Korhonen</span></p>
    <p class="credential">PhD</p>
  </div>

  <div class="front-wordmark">Coastal Tundrabridge<br>Advisory</div>

  <address class="address" style="font-style:normal">
    PO Box 418259<br>
    Quillwater, Alaska 99642
  </address>

  <ul class="contacts">
    <li>+1-907-555-0143
      <svg viewBox="0 0 24 24" aria-hidden="true"><path d="M6.6 10.8a15 15 0 0 0 6.6 6.6l2.2-2.2a1 1 0 0 1 1-.25 11.4 11.4 0 0 0 3.6.57 1 1 0 0 1 1 1V20a1 1 0 0 1-1 1A17 17 0 0 1 3 4a1 1 0 0 1 1-1h3.5a1 1 0 0 1 1 1c0 1.25.2 2.45.57 3.57a1 1 0 0 1-.25 1z"/></svg>
    </li>
    <li>mkorhonen@tundrabridgeadvisory.example
      <svg viewBox="0 0 24 24" aria-hidden="true"><path d="M2 5h20v14H2zm2 2v.5l8 5 8-5V7zm0 2.8V17h16V9.8l-8 5z"/></svg>
    </li>
    <li>www.coastaltundrabridgeadvisory.example
      <svg viewBox="0 0 24 24" aria-hidden="true"><path d="M12 2a10 10 0 1 0 0 20 10 10 0 0 0 0-20zm0 2c.9 0 2.2 1.9 2.7 5H9.3C9.8 5.9 11.1 4 12 4zm-3 .6A11 11 0 0 0 7.3 9H4.6A8 8 0 0 1 9 4.6zm6 0A8 8 0 0 1 19.4 9h-2.7A11 11 0 0 0 15 4.6zM4.1 11h3.1a17 17 0 0 0 0 2H4.1a8 8 0 0 1 0-2zm5.1 0h5.6a15 15 0 0 1 0 2H9.2a15 15 0 0 1 0-2zm7.6 0h3.1a8 8 0 0 1 0 2h-3.1a17 17 0 0 0 0-2zM4.6 15h2.7A11 11 0 0 0 9 19.4 8 8 0 0 1 4.6 15zm4.7 0h5.4c-.5 3.1-1.8 5-2.7 5s-2.2-1.9-2.7-5zm7.4 0h2.7A8 8 0 0 1 15 19.4a11 11 0 0 0 1.7-4.4z"/></svg>
    </li>
  </ul>
</section>

</body>
</html>
```